K7 Electrical Services Ltd Web design

I require a web site for my new electrical contracting company. We are customer service orientated. Offering high value electrical installations, design and maintenance. Focused on custom residential and commercial upgrading. Lighting design and application are paramount in our company's services. Industry leading product use and integration are always on the forefront with our customer client services. As well as energy efficiency.

Target Market(s)

Homebuilders, General Contractors, Property management companies, clients, individuals,

Industry/Entity Type

Electric Company

Coding

Coded - Design and coding required

Number of Pages Required

3 page

Requirements
Must have
• Classic, modern, edgy but not trendy . Appeals to the masse.
• 3 page
• home page
• about page
• gallery page
• ability to contact from the webiste
Nice to have
• open to all types of designs that are relative to the construction industry.
• Black, Grey, metallic ice blue and deep purple colours from the logo.
Should not have
• anything cheesy with cartoon light bulb images.

```html
<!DOCTYPE html>
<html lang="en">
<head>
<meta charset="utf-8">
<title>K7 Electrical Services Ltd</title>
<link href="https://fonts.googleapis.com/css2?family=Montserrat:wght@400;500;600;700&family=Open+Sans:wght@400;600&display=swap" rel="stylesheet">
<style>
:root{
  --purple:#7c3c9c;
  --purple-dark:#5f2a7c;
  --ink:#222222;
  --dark:#2b2b2b;
  --darker:#1f1f1f;
  --grey:#6b6b6b;
  --line:#4a4a4a;
  --white:#ffffff;
}
*{box-sizing:border-box;margin:0;padding:0}
html,body{width:1200px;height:3854px;overflow:hidden}
body{font-family:"Open Sans",Arial,sans-serif;color:var(--ink);background:var(--white);position:relative}
.head-font{font-family:"Montserrat",Arial,sans-serif}

/* top bar */
.topbar{height:36px;background:var(--dark);color:#e6e6e6;display:flex;align-items:center;justify-content:space-between;padding:0 98px;font-size:12px;font-family:"Montserrat",Arial,sans-serif}
.topbar .addr{display:flex;align-items:center;gap:8px}
.topbar .social{display:flex;gap:8px}
.topbar .social span{width:16px;height:16px;border-radius:50%;background:#555}
.topbar .social span:first-child{background:var(--purple)}

/* header */
.header{height:108px;display:flex;align-items:center;justify-content:space-between;padding:0 98px}
.contact-mini{display:flex;align-items:center;gap:14px;font-size:12px;font-family:"Montserrat",Arial,sans-serif}
.contact-mini .ico{width:44px;height:44px;border:1px solid #ddd;border-radius:6px;display:flex;align-items:center;justify-content:center}
.contact-mini b{display:block;color:var(--purple);font-weight:500;font-size:12px}
.contact-mini small{color:#888;font-size:12px}
.contact-mini.right{text-align:left}
.brand{display:flex;align-items:center;gap:10px;font-family:"Montserrat",Arial,sans-serif;font-weight:700;color:var(--purple);font-size:26px;letter-spacing:1px}
.brand .mark{width:18px;height:18px;background:var(--purple)}

/* hero */
.hero{position:relative;height:666px;background:linear-gradient(100deg,#9aa3ad 0%,#c9ced3 45%,#e8e4dc 75%,#f2efeb 100%)}
.nav{position:absolute;left:98px;right:100px;top:0;height:51px;background:var(--purple);display:flex;align-items:center;z-index:2}
.nav .home{width:51px;height:51px;background:var(--darker);display:flex;align-items:center;justify-content:center}
.nav ul{list-style:none;display:flex;gap:0;margin-left:22px;flex:1}
.nav li{color:#fff;font-family:"Montserrat",Arial,sans-serif;font-weight:600;font-size:13px;padding:0 18px}
.nav .search{margin-right:22px}
.nav .quote{background:var(--darker);color:#fff;font-family:"Montserrat",Arial,sans-serif;font-weight:600;font-size:12px;padding:11px 16px;margin-right:10px}
.hero-text{position:absolute;left:98px;top:190px;color:#fff;z-index:2}
.hero-text .eyebrow{font-family:"Montserrat",Arial,sans-serif;font-size:20px;font-weight:500}
.hero-text h1{font-family:"Montserrat",Arial,sans-serif;font-size:46px;font-weight:700;margin:4px 0 10px}
.hero-text p{font-size:15px;font-weight:600;line-height:22px;width:560px}
.hero-text .btns{display:flex;gap:10px;margin-top:44px}
.btn{font-family:"Montserrat",Arial,sans-serif;font-size:12px;font-weight:700;color:#fff;padding:12px 18px}
.btn.purple{background:var(--purple)}
.btn.dark{background:var(--darker)}

/* solution cards */
.solutions{position:absolute;top:730px;left:182px;display:flex;gap:36px}
.sol{width:398px;height:285px;background:#fff}
.sol .pic{height:226px}
.sol .label{height:59px;background:var(--purple);color:#fff;display:flex;align-items:center;gap:14px;padding:0 20px;font-family:"Montserrat",Arial,sans-serif;font-weight:700;font-size:17px;letter-spacing:.5px}

/* who we are */
.section-title{text-align:center;font-family:"Montserrat",Arial,sans-serif;font-size:30px;font-weight:600;color:var(--ink)}
.section-title em{font-style:normal;color:var(--purple)}
.section-title + .rule{width:60px;height:2px;background:var(--purple);margin:12px auto 0}
.who{position:absolute;top:1088px;left:0;width:1200px;height:616px}
.who .intro{width:1040px;margin:38px auto 0;text-align:center;font-size:13px;line-height:22px;color:#444}
.who .worker{position:absolute;left:205px;top:184px;width:258px;height:432px;background:linear-gradient(180deg,#f0c419 0%,#f2a33a 35%,#ea6b2c 60%,#3a3a3a 100%);border-radius:120px 120px 0 0}
.features{position:absolute;left:552px;top:208px;width:500px}
.feature{display:flex;gap:26px;height:128px}
.feature .circle{width:64px;height:64px;border-radius:50%;background:#fff;box-shadow:0 2px 10px rgba(0,0,0,.12);display:flex;align-items:center;justify-content:center;flex:none}
.feature h3{font-family:"Montserrat",Arial,sans-serif;font-size:14px;font-weight:700;margin-top:6px}
.feature p{font-size:12px;line-height:20px;color:#555;margin-top:8px}

/* services */
.services{position:absolute;top:1704px;left:0;width:1200px;height:673px;background:var(--dark);color:#fff}
.services .section-title{color:#fff;margin-top:64px}
.grid{position:absolute;left:98px;top:167px;width:1002px;display:grid;grid-template-columns:repeat(3,1fr)}
.svc{height:216px;text-align:center;padding-top:2px;font-size:13px;line-height:21px;color:#ddd}
.svc:nth-child(-n+3){border-bottom:1px solid var(--line)}
.svc:nth-child(3n+1),.svc:nth-child(3n+2){border-right:1px solid var(--line)}
.svc:nth-child(n+4){padding-top:30px}
.svc svg{display:block;margin:0 auto 14px}
.svc h3{font-family:"Montserrat",Arial,sans-serif;font-size:15px;font-weight:600;color:#fff;margin-bottom:4px}
.svc p{width:250px;margin:0 auto}

/* projects */
.projects{position:absolute;top:2377px;left:0;width:1200px;height:740px}
.projects .section-title{margin-top:78px}
.tiles{position:absolute;left:98px;top:178px;width:1002px;display:grid;grid-template-columns:repeat(3,318px);grid-template-rows:223px 223px;column-gap:24px;row-gap:26px}
.tile{position:relative}
.tile.active{background:var(--purple);color:#fff;display:flex;flex-direction:column;align-items:center;justify-content:center;gap:20px;font-family:"Montserrat",Arial,sans-serif;font-weight:600;font-size:13px}
.tile.active .zoom{width:28px;height:28px;border:1px solid #fff;border-radius:50%;display:flex;align-items:center;justify-content:center}

/* quote band */
.quote-band{position:absolute;top:3117px;left:0;width:1200px;height:137px;background:var(--purple);color:#fff;font-family:"Montserrat",Arial,sans-serif}
.quote-band .call{position:absolute;left:106px;top:30px}
.quote-band .call h4{font-size:26px;font-weight:600}
.quote-band .call strong{font-size:38px;font-weight:700;display:block;margin-top:4px}
.quote-band .divider{position:absolute;left:432px;top:24px;width:1px;height:90px;background:rgba(255,255,255,.4)}
.quote-band .news{position:absolute;left:466px;top:24px}
.quote-band .news h4{font-size:28px;font-weight:600}
.quote-band form{display:flex;gap:14px;margin-top:14px}
.field{width:272px;height:46px;background:#fff;color:#888;font-size:13px;padding:0 12px;display:flex;align-items:center;font-family:"Open Sans",Arial,sans-serif}
.go{width:56px;height:46px;background:var(--darker);color:#fff;font-weight:700;font-size:18px;display:flex;align-items:center;justify-content:center}

/* footer */
.footer{position:absolute;top:3254px;left:0;width:1200px;height:560px;background:var(--dark);color:#fff;text-align:center}
.footer .brand{color:#fff;justify-content:center;margin-top:110px;font-size:30px}
.footer .brand .mark{background:#fff}
.contacts{position:absolute;top:250px;left:98px;width:1002px;display:grid;grid-template-columns:repeat(3,1fr)}
.contact .pin{width:56px;height:56px;border-radius:50%;background:var(--purple);margin:0 auto;display:flex;align-items:center;justify-content:center}
.contact h5{font-family:"Montserrat",Arial,sans-serif;font-size:15px;font-weight:700;margin:26px 0 14px}
.contact p{font-size:12.5px;line-height:20px;color:#e5e5e5}
.footer .socials{position:absolute;top:506px;left:0;width:1200px;display:flex;justify-content:center;gap:20px}
.footer .socials span{width:20px;height:20px;border-radius:50%;background:#fff}
.copyright{position:absolute;top:3814px;left:0;width:1200px;height:40px;background:var(--purple);color:#fff;font-size:13px;display:flex;align-items:center;justify-content:center}
</style>
</head>
<body>

<div class="topbar">
  <div class="addr">
    <svg width="12" height="16" viewBox="0 0 12 16"><path d="M6 0C2.7 0 0 2.6 0 5.8 0 10 6 16 6 16s6-6 6-10.2C12 2.6 9.3 0 6 0zm0 8.2A2.3 2.3 0 1 1 6 3.6a2.3 2.3 0 0 1 0 4.6z" fill="#9b59c0"/></svg>
    Level 4, Suite 12 88 Harbour Lane Southbank, Victoria 3006
  </div>
  <div class="social" aria-label="Social links"><span></span><span></span><span></span><span></span><span></span></div>
</div>

<header class="header">
  <div class="contact-mini">
    <div class="ico"><svg width="22" height="16" viewBox="0 0 22 16"><rect x="1" y="1" width="20" height="14" fill="none" stroke="#7c3c9c" stroke-width="1.6"/><path d="M1 1l10 8 10-8" fill="none" stroke="#7c3c9c" stroke-width="1.6"/></svg></div>
    <div><b>Send Mail Us</b><small>info@k7electricalservices.com</small></div>
  </div>
  <div class="brand"><span class="mark"></span>K7 ELECTRICAL SERVICES</div>
  <div class="contact-mini right">
    <div class="ico"><svg width="18" height="18" viewBox="0 0 24 24"><path d="M6.6 10.8a15.1 15.1 0 0 0 6.6 6.6l2.2-2.2c.3-.3.7-.4 1-.2 1.1.4 2.3.6 3.6.6.6 0 1 .4 1 1V20c0 .6-.4 1-1 1C10.6 21 3 13.4 3 4c0-.6.4-1 1-1h3.5c.6 0 1 .4 1 1 0 1.3.2 2.5.6 3.6.1.3 0 .7-.2 1z" fill="none" stroke="#7c3c9c" stroke-width="1.6"/></svg></div>
    <div><b>Call Us Now</b><small>+61 1300 555 718</small></div>
  </div>
</header>

<section class="hero" role="img" aria-label="Photo of an electrician in a purple cap wiring a distribution board">
  <nav class="nav">
    <div class="home"><svg width="20" height="18" viewBox="0 0 20 18"><path d="M10 0L0 9h3v9h5v-6h4v6h5V9h3z" fill="#fff"/></svg></div>
    <ul><li>FEATURES</li><li>RESIDENTIAL</li><li>COMMERCIAL</li><li>REVIEWS</li><li>CONTACT US</li></ul>
    <svg class="search" width="18" height="18" viewBox="0 0 18 18"><circle cx="7.5" cy="7.5" r="6" fill="none" stroke="#fff" stroke-width="2"/><path d="M12 12l5 5" stroke="#fff" stroke-width="2"/></svg>
    <div class="quote">GET A QUOTE</div>
  </nav>
  <div class="hero-text">
    <div class="eyebrow">K7 Electrical Services</div>
    <h1>Fast Electrical Services!</h1>
    <p>Universal business theme continues to grow continues to grow ever day thanks to the confidence our clients have in us.</p>
    <div class="btns"><span class="btn purple">OUR COMPANY</span><span class="btn dark">CONTACT US</span></div>
  </div>
</section>

<div class="solutions">
  <div class="sol">
    <div class="pic" role="img" aria-label="Photo of a modern two-storey home at dusk" style="background:linear-gradient(180deg,#3f6fb0 0%,#8aa7c9 45%,#d8b27a 75%,#b58a55 100%)"></div>
    <div class="label"><svg width="22" height="24" viewBox="0 0 22 24"><path d="M11 4a6 6 0 0 0-3.5 10.9V18h7v-3.1A6 6 0 0 0 11 4zM8 20h6M9 22.5h4M11 0v2M2 4l1.5 1.5M20 4l-1.5 1.5" fill="none" stroke="#fff" stroke-width="1.5"/></svg>RESIDENTIAL SOLUTION</div>
  </div>
  <div class="sol">
    <div class="pic" role="img" aria-label="Photo of hands wiring a commercial switchboard" style="background:linear-gradient(160deg,#6b8fb3 0%,#c7cfd6 40%,#d9a64a 70%,#8a6b4a 100%)"></div>
    <div class="label"><svg width="22" height="24" viewBox="0 0 22 24"><path d="M11 4a6 6 0 0 0-3.5 10.9V18h7v-3.1A6 6 0 0 0 11 4zM8 20h6M9 22.5h4M11 0v2M2 4l1.5 1.5M20 4l-1.5 1.5" fill="none" stroke="#fff" stroke-width="1.5"/></svg>COMMERCIAL SOLUTION</div>
  </div>
</div>

<section class="who">
  <h2 class="section-title">Who <em>We Are</em></h2>
  <div class="rule"></div>
  <p class="intro">Lorem Ipsum is simply dummy text of the printing and typesetting industry. Lorem Ipsum has been the industry's standard dummy text ever since the 1500s, when an unknown printer took a galley of type and scrambled it to make a type specimen book. It has survived not only five centuries.</p>
  <div class="worker" role="img" aria-label="Photo of an electrician in a hard hat and hi-vis vest, arms crossed"></div>
  <div class="features">
    <div class="feature">
      <div class="circle"><svg width="34" height="34" viewBox="0 0 34 34"><circle cx="17" cy="17" r="14" fill="none" stroke="#7c3c9c" stroke-width="2"/><text x="17" y="21" text-anchor="middle" font-family="Montserrat,Arial,sans-serif" font-size="11" font-weight="700" fill="#7c3c9c">24</text></svg></div>
      <div><h3>SAVE TIME</h3><p>Our team of experts will determine your needs and develop a 100% custom migration strategy tailored to your company. ....</p></div>
    </div>
    <div class="feature">
      <div class="circle"><svg width="30" height="30" viewBox="0 0 30 30"><path d="M6 24l6-6M10 14l6 6 8-8-6-6zM18 6l3-3M24 12l3-3" fill="none" stroke="#7c3c9c" stroke-width="2"/></svg></div>
      <div><h3>SAVE EFFORT</h3><p>After identifying your needs, we will start migrating your data. Your email service will be re-routed to WorkSuite....</p></div>
    </div>
    <div class="feature">
      <div class="circle"><svg width="32" height="24" viewBox="0 0 32 24"><rect x="2" y="3" width="28" height="18" fill="none" stroke="#7c3c9c" stroke-width="2"/><circle cx="16" cy="12" r="4" fill="#7c3c9c"/></svg></div>
      <div><h3>SAVE MONEY</h3><p>Migrating your data to WorkSuite means cutting down on expenses and boosting your performance. Plus, we offer you.....</p></div>
    </div>
  </div>
</section>

<section class="services">
  <h2 class="section-title" style="color:#fff">AWESOME <em>SERVICES</em></h2>
  <div class="rule"></div>
  <div class="grid">
    <div class="svc">
      <svg width="44" height="52" viewBox="0 0 44 52"><path d="M10 2h24l6 24H4z" fill="#fff"/><rect x="20" y="26" width="4" height="18" fill="#fff"/><rect x="10" y="44" width="24" height="5" fill="#fff"/></svg>
      <h3>ELECTRICAL</h3><p>No Need To Recreate Your Active Directory. Lorem Ipsum has been the industry's standard</p>
    </div>
    <div class="svc">
      <svg width="52" height="52" viewBox="0 0 52 52"><g fill="none" stroke="#fff" stroke-width="3"><path d="M8 10v34M17 10v34M26 10v34M35 10v34M44 10v34M4 38h44"/></g></svg>
      <h3>HEATING</h3><p>All Email And Data From Virtually All Email Platform. Lorem Ipsum has been the industry's standard</p>
    </div>
    <div class="svc">
      <svg width="52" height="52" viewBox="0 0 52 52"><rect x="3" y="3" width="46" height="46" fill="none" stroke="#fff" stroke-width="3"/><circle cx="26" cy="26" r="14" fill="none" stroke="#fff" stroke-width="3"/><path d="M21 18v16M26 16v20M31 18v16" stroke="#fff" stroke-width="2"/></svg>
      <h3>AIR CONDITIONING</h3><p>Data Storage to DriveBox Cloud Storage. Lorem Ipsum has been the industry's standard dummy</p>
    </div>
    <div class="svc">
      <svg width="60" height="46" viewBox="0 0 60 46"><path d="M6 8l40 10-4 12L4 20z" fill="#fff"/><path d="M44 22l10 4-2 6-10-4" fill="#fff"/><path d="M14 24v14H4" fill="none" stroke="#fff" stroke-width="3"/></svg>
      <h3>SECURITY SYSTEMS</h3><p>From TeamPoint To TeamPoint Online. Lorem Ipsum has been the industry's standard dummy</p>
    </div>
    <div class="svc">
      <svg width="52" height="52" viewBox="0 0 52 52"><rect x="12" y="12" width="28" height="28" fill="none" stroke="#fff" stroke-width="3"/><rect x="19" y="19" width="14" height="14" fill="#fff"/><path d="M18 4v8M26 4v8M34 4v8M18 40v8M26 40v8M34 40v8M4 18h8M4 26h8M4 34h8M40 18h8M40 26h8M40 34h8" stroke="#fff" stroke-width="2.5"/></svg>
      <h3>PANELS CHANGES</h3><p>Migrating from one WorkSuite tenant to another WorkSuite tenant for Acquisitions &amp; Mergers Lorem Ipsum.</p>
    </div>
    <div class="svc">
      <svg width="52" height="52" viewBox="0 0 52 52"><path d="M8 8l36 36M44 8L8 44" stroke="#fff" stroke-width="5" stroke-linecap="round"/><circle cx="10" cy="10" r="6" fill="none" stroke="#fff" stroke-width="3"/></svg>
      <h3>TROUBLE SHOOTING</h3><p>Lorem Ipsum has been the industry's standard dummy text ever since the 1500s, when an unknown printer</p>
    </div>
  </div>
</section>

<section class="projects">
  <h2 class="section-title">Latest <em>Projects</em></h2>
  <div class="rule"></div>
  <div class="tiles">
    <div class="tile active" role="img" aria-label="Residential solution project, purple overlay">
      RESIDENTIAL SOLUTION
      <span class="zoom"><svg width="12" height="12" viewBox="0 0 12 12"><circle cx="5" cy="5" r="3.5" fill="none" stroke="#fff" stroke-width="1.4"/><path d="M7.5 7.5l3 3" stroke="#fff" stroke-width="1.4"/></svg></span>
    </div>
    <div class="tile" role="img" aria-label="Photo of an electrician in a hard hat wiring a panel" style="background:linear-gradient(135deg,#c9c3b3,#8c8a86 55%,#2e3338)"></div>
    <div class="tile" role="img" aria-label="Photo of a technician servicing a wall air conditioner" style="background:linear-gradient(135deg,#eef0f2,#c3cad1 55%,#7f8d99)"></div>
    <div class="tile" role="img" aria-label="Photo of a screwdriver fixing circuit breakers" style="background:linear-gradient(135deg,#f2f2f2,#d2d4d6 55%,#c4623a)"></div>
    <div class="tile" role="img" aria-label="Photo of an electrician fitting a wall socket" style="background:linear-gradient(135deg,#ece6da,#c7b9a2 55%,#5b87b0)"></div>
    <div class="tile" role="img" aria-label="Photo of an electrician in a yellow hard hat testing wiring" style="background:linear-gradient(135deg,#e7eaf0,#9aa5b5 50%,#d6d23a)"></div>
  </div>
</section>

<section class="quote-band">
  <div class="call"><h4>GET FREE QUOTE</h4><strong>1300 555 718</strong></div>
  <div class="divider"></div>
  <div class="news">
    <h4>SUBSCRIBE TO NEWSLETTER</h4>
    <form><span class="field">Your Name</span><span class="field">Type Your Email</span><span class="go">GO</span></form>
  </div>
</section>

<footer class="footer">
  <div class="brand"><span class="mark"></span>K7 ELECTRICAL SERVICES</div>
  <div class="contacts">
    <div class="contact">
      <div class="pin"><svg width="14" height="20" viewBox="0 0 12 16"><path d="M6 0C2.7 0 0 2.6 0 5.8 0 10 6 16 6 16s6-6 6-10.2C12 2.6 9.3 0 6 0zm0 8.2A2.3 2.3 0 1 1 6 3.6a2.3 2.3 0 0 1 0 4.6z" fill="#fff"/></svg></div>
      <h5>ADDRESS</h5><p>Northside Studio Works<br>45-47 Kerr Street<br>Fitzroy VIC 3065</p>
    </div>
    <div class="contact">
      <div class="pin"><svg width="18" height="18" viewBox="0 0 24 24"><path d="M6.6 10.8a15.1 15.1 0 0 0 6.6 6.6l2.2-2.2c.3-.3.7-.4 1-.2 1.1.4 2.3.6 3.6.6.6 0 1 .4 1 1V20c0 .6-.4 1-1 1C10.6 21 3 13.4 3 4c0-.6.4-1 1-1h3.5c.6 0 1 .4 1 1 0 1.3.2 2.5.6 3.6.1.3 0 .7-.2 1z" fill="#fff"/></svg></div>
      <h5>PHONE</h5><p>+ 03 9560 1184, + 03 9560 1184,<br>+ 03 9560 1184.</p>
    </div>
    <div class="contact">
      <div class="pin"><svg width="20" height="14" viewBox="0 0 22 16"><rect x="1" y="1" width="20" height="14" fill="none" stroke="#fff" stroke-width="1.8"/><path d="M1 1l10 8 10-8" fill="none" stroke="#fff" stroke-width="1.8"/></svg></div>
      <h5>ADDRESS</h5><p>admin@k7electricalservices.com<br>info@k7electricalservices.com</p>
    </div>
  </div>
  <div class="socials" aria-label="Social links"><span></span><span></span><span></span></div>
</footer>

<div class="copyright">© Copyright 2018 k7electricalservices.com | All Rights Reserved</div>

</body>
</html>
```